Active Mentors UK award course Flyer Design

Flyer design required for a social enterprise called "Backing Play" - logo attached - to promote our Active Mentors Award course(s).

The course is targeted at individuals aged 13+ and will develop leadership skills that transfer beyond the sporting environment. It is a fun and practical course that focusses on leading rather than sporting ability or technical knowledge and leads on to further qualifications or awards. Individuals' self-confidence will improve and the course is a potential stepping stone in to employment, further education or training.

The course will be run at Brookfield Community Sports Centre, Ashcombe School, Pellow Lane, Kenilworth. CV7 4RX. On Monday 20th July to Friday 24th July.
There is a subsidised fee of £15

We are a Regional Academy for Active Mentors UK.

The company's main colour is royal blue but please make the design as attractive and eye-catching to young people, male and female, as possible.

```html
<!DOCTYPE html>
<html lang="en">
<head>
<meta charset="utf-8">
<title>Active Mentors Award Course Flyer</title>
<link rel="stylesheet" href="https://fonts.googleapis.com/css2?family=Arimo:wght@400;700&display=swap">
<style>
  :root {
    --page-bg: #8f948d;
    --royal: #1a4fa3;
    --royal-deep: #143f88;
    --navy: #1a1f2e;
    --headline-navy: #1f3585;
    --sky: #5ab4f0;
    --pale-sky: #8fcdf2;
    --band-text: #dfe5f0;
    --white: #ffffff;
    --ink: #1b1e26;
  }
  html, body {
    margin: 0;
    width: 1200px;
    height: 900px;
    overflow: hidden;
    background: var(--page-bg);
    font-family: "Arimo", Arial, sans-serif;
  }
  .flyer {
    position: absolute;
    left: 152px;
    top: 185px;
    width: 886px;
    height: 627px;
    box-shadow: 0 6px 18px rgba(0,0,0,0.35);
  }
  .flyer svg { display: block; }
  .txt { font-family: "Arimo", Arial, sans-serif; }
  .tagline { font-size: 27px; fill: var(--ink); }
  .tagline .lead { fill: var(--headline-navy); }
  .band-title { font-size: 34px; font-weight: 700; fill: var(--band-text); }
  .venue-name { font-size: 23px; font-weight: 700; fill: var(--white); }
  .venue-address { font-size: 21px; fill: var(--white); }
  .dates { font-size: 26px; fill: var(--white); }
  .dates .day { fill: var(--sky); }
  .dates .small { font-size: 18px; }
  .more { font-size: 20px; fill: var(--white); }
  .url { font-size: 24px; fill: var(--white); }
  .brand-name { font-size: 30px; font-weight: 700; fill: var(--royal); }
</style>
</head>
<body>
<main class="flyer">
  <svg width="886" height="627" viewBox="0 0 886 627" xmlns="http://www.w3.org/2000/svg">
    <defs>
      <linearGradient id="hallTone" x1="0" y1="0" x2="0" y2="1">
        <stop offset="0" stop-color="#d8d2c2"/>
        <stop offset="0.12" stop-color="#ebe8e1"/>
        <stop offset="0.22" stop-color="#f1f0ec"/>
        <stop offset="0.26" stop-color="#3a4a8c"/>
        <stop offset="0.33" stop-color="#2f3f80"/>
        <stop offset="0.37" stop-color="#d9c3a2"/>
        <stop offset="0.6" stop-color="#caa77c"/>
        <stop offset="1" stop-color="#b58d60"/>
      </linearGradient>
    </defs>

    <rect class="hero-photo" x="0" y="0" width="886" height="627" fill="url(#hallTone)"
          role="img" aria-label="Photo: young players in a sports hall, one raising a volleyball above the net"/>

    <text class="txt tagline" x="460" y="66"><tspan class="lead">LESSON 2:</tspan> STAY FOCUSED.</text>

    <!-- left blue wedge -->
    <polygon class="wedge" points="0,145 280,380 280,627 0,627" fill="var(--royal)"/>
    <polygon class="wedge-shade" points="0,300 280,470 280,627 0,627" fill="var(--royal-deep)"/>

    <!-- dark info panel -->
    <polygon class="info-panel" points="280,445 886,240 886,627 280,627" fill="var(--navy)"/>

    <!-- title band -->
    <polygon class="title-band" points="263,360 886,145 886,240 288,445" fill="var(--royal)"/>

    <!-- accent lines -->
    <line x1="38" y1="375" x2="148" y2="335" stroke="var(--white)" stroke-width="5"/>
    <line x1="50" y1="390" x2="125" y2="362" stroke="var(--white)" stroke-width="5"/>

    <!-- logo card -->
    <polygon class="logo-card" points="0,413 260,327 312,515 40,608" fill="var(--white)"/>
    <polygon class="logo-card-bar" points="48,580 268,510 278,545 58,615" fill="var(--white)"/>
    <g class="brand">
      <circle cx="52" cy="470" r="14" fill="var(--pale-sky)"/>
      <text class="txt brand-name" x="74" y="481">Backing Play</text>
    </g>

    <!-- rotated copy -->
    <g transform="translate(303,412) rotate(-20)">
      <text class="txt band-title" x="0" y="0">ACTIVE MENTORS AWARD COURSE</text>
    </g>
    <g transform="translate(356,477) rotate(-20)">
      <text class="txt venue-name" x="0" y="0">BROOKFIELD COMMUNITY SPORTS CENTRE</text>
      <text class="txt venue-address" x="62" y="26">PELLOW LANE, KENILWORTH. CV7 4RX</text>
    </g>
    <g transform="translate(383,558) rotate(-20)">
      <text class="txt dates" x="0" y="0"><tspan class="day">MONDAY</tspan>20TH JULY <tspan class="small">TO</tspan> <tspan class="day">FRIDAY</tspan>24TH JULY</text>
    </g>

    <!-- web bar -->
    <polygon class="web-bar" points="543,565 886,452 886,505 558,610" fill="var(--royal)"/>
    <g transform="translate(616,527) rotate(-20)">
      <text class="txt more" x="0" y="0">Find out more at</text>
    </g>
    <g transform="translate(575,588) rotate(-20)">
      <text class="txt url" x="0" y="0">www.backingplay.org</text>
    </g>
  </svg>
</main>
</body>
</html>
```